Textbook cover for educational dental hygiene seminar

A professional and trendy textbook cover design to be used. 8.5 x 11 with full bleed, cmyk, and a count for binding when designed. Year 2023 displayed, and title BexlerRDH’s Dental Hygiene Academy. Colors- shades of purple, white, and black. Please also use logo. Website www.BexlerRDHExamPrep.example

For background- maybe ombré, or some sort of trendy design. Display a big tooth on the front.

Colors
6B429C
8869AF
B7A5CE
E3DAEB
F3F0F8

```html
<!DOCTYPE html>
<html lang="en">
<head>
<meta charset="utf-8">
<title>BexlerRDH’s Dental Hygiene Academy 2023</title>
<link href="https://fonts.googleapis.com/css2?family=Bebas+Neue&display=swap" rel="stylesheet">
<style>
  :root {
    --cover-purple: #8c21bc;
    --tooth-shade: #45164f;
    --year-ghost: rgba(40, 0, 60, 0.14);
    --title-white: #ffffff;
    --year-black: #000000;
    --seal-navy: #33205f;
  }
  html, body {
    margin: 0;
    padding: 0;
    overflow: hidden;
    background: var(--cover-purple);
  }
  .cover {
    display: block;
    width: 927px;
    height: 1200px;
  }
  .cover-background { fill: var(--cover-purple); }
  .tooth-area { fill: var(--tooth-shade); }
  .year-ghost {
    fill: var(--year-ghost);
    font-family: "Bebas Neue", sans-serif;
    font-size: 480px;
  }
  .cover-title {
    fill: var(--title-white);
    font-family: "Bebas Neue", sans-serif;
    font-size: 194px;
  }
  .cover-title .title-lead { font-size: 180px; }
  .cover-year {
    fill: var(--year-black);
    font-family: "Bebas Neue", sans-serif;
    font-size: 117px;
    stroke: var(--year-black);
    stroke-width: 2px;
  }
  .academy-seal { fill: var(--seal-navy); }
  .academy-name {
    fill: var(--title-white);
    font-family: "Bebas Neue", sans-serif;
    font-size: 30px;
  }
</style>
</head>
<body>
<svg class="cover" viewBox="0 0 927 1200" xmlns="http://www.w3.org/2000/svg">
  <rect class="cover-background" x="0" y="0" width="927" height="1200"/>

  <rect class="tooth-area" x="567" y="350" width="420" height="900" rx="190"
        role="img" aria-label="Large tooth illustration in dark purple"/>

  <text class="year-ghost" x="20" y="1370" textLength="900" lengthAdjust="spacingAndGlyphs">2023</text>

  <text class="cover-title">
    <tspan class="title-lead" x="79" y="259">BEXLERRDH’S</tspan>
    <tspan x="84" y="430">DENTAL</tspan>
    <tspan x="84" y="603">HYGIENE</tspan>
    <tspan x="79" y="775">ACADEMY</tspan>
  </text>

  <text class="cover-year" x="81" y="1133">2023</text>

  <g class="academy-mark">
    <circle class="academy-seal" cx="791" cy="1076" r="74"/>
    <text class="academy-name" x="791" y="1087" text-anchor="middle">BexlerRDH</text>
  </g>
</svg>
</body>
</html>
```